Stationery Design Project for Marketing Consultancy

I have started a new consultancy business and require the following elements to be designed using existing logo:
• Business card
• Letterhead
• Envelope (DL, C4, C5)
• Microsoft word template for report writing
• A4 Presentation Folder
• Powerpoint template
COPY FOR FRONT AND BACK OF BUSINESS CARD
logo
'Measurable Marketing. Epic Results' slogan (but no need to use existing lockup with logo)
name, B Bus. Mktg, Grad Dip Digital Mktg, CPM (post nominal abbreviations in smaller font)
mobile: 04XX-XXX-XXX (I will give details to the winner to add)
website: www.tolvarin.com.au
email: info@tolvarin.com.au
COPY FOR LETTERHEAD
Logo
Company Name
Please, submit your designs that include business card, letterhead and envelope. Once selected the winner will be asked to complete the project by creating the rest of the artwork.
FINAL FILES
Print ready files to be supplied as well as Indesign files so that minor amends can be made if necessary in future.
• Layered vectors in EPS & PDF
• Screen quality JPEG & PNGs
ABOUT THE BUSINESS: TOLVARIN
I work with clients to understand their business challenges, developing and executing measurable marketing strategies tied to key business metrics. Services include:
Services include:
• Business planning and business development
• Marketing and brand strategy
• Insight-driven integrated campaigns
• Loyalty programs and retention marketing
• Marketing automation
• Direct marketing (traditional and digital)
• Content strategy and development
Hi everyone,
Target Market(s)
Corporate decision makers (heads of marketing, general managers etc) and small to medium sized business owners. Predominately male aged 35+
Industry/Entity Type
Marketing
Requirements
Must have
- BRAND PERSONALITY
The successful design will communicate brand personality. I am a professional, results-driven entrepreneur, but want to show off my creative flair.
MEMORABILITY
Looking for a unique and eye-catching design. Am considering special printing effects (die cuts, letterpress, interactive elements, embossing, foiling etc) or a striking minimalist approach.
Nice to have
- I have a mission that could be incorporated on reverse if room -
Turning insights into actions & passion into profit.
Should not have
- Use of pink or green.

```html
<!DOCTYPE html>
<html lang="en">
<head>
<meta charset="utf-8">
<title>Tolvarin – Business Card</title>
<link href="https://fonts.googleapis.com/css2?family=PT+Sans:wght@400;700&display=swap" rel="stylesheet">
<style>
  :root {
    --backdrop: #e6e4e1;
    --card: #ffffff;
    --charcoal: #3d3d3f;
    --mid-grey: #8a8a8c;
    --soft-grey: #c9c9cb;
    --ink: #1e1e1e;
    --shadow: rgba(0, 0, 0, 0.28);
  }
  * { margin: 0; padding: 0; box-sizing: border-box; }
  html, body {
    width: 1200px;
    height: 1124px;
    overflow: hidden;
    background: var(--backdrop);
    font-family: "PT Sans", sans-serif;
    color: var(--ink);
  }
  .stationery {
    position: relative;
    width: 1200px;
    height: 1124px;
  }
  .card {
    position: absolute;
    width: 560px;
    height: 340px;
    background: var(--card);
    overflow: hidden;
    box-shadow: 0 10px 28px var(--shadow);
  }
  .card__waves {
    position: absolute;
    inset: 0;
    width: 100%;
    height: 100%;
  }
  .card--front { left: 250px; top: 170px; }
  .card--back  { left: 400px; top: 610px; }

  .brand {
    position: absolute;
    display: flex;
    align-items: center;
    gap: 14px;
  }
  .brand__dot {
    width: 44px;
    height: 44px;
    border-radius: 50%;
    background: var(--charcoal);
  }
  .brand__name {
    font-weight: 700;
    font-size: 52px;
    letter-spacing: 2px;
    color: var(--charcoal);
    line-height: 1;
  }
  .card--front .brand { left: 120px; top: 142px; }

  .card--back .brand { right: 36px; top: 38px; gap: 8px; }
  .card--back .brand__dot { width: 20px; height: 20px; }
  .card--back .brand__name { font-size: 22px; letter-spacing: 1px; }

  .contact {
    position: absolute;
    left: 70px;
    top: 120px;
    line-height: 1.3;
  }
  .contact__name { font-size: 20px; font-weight: 400; }
  .contact__role { font-size: 14px; }
  .contact__post { font-size: 12.5px; }
  .contact__line { font-size: 14px; }
  .contact__web { font-size: 15px; font-weight: 700; margin-top: 4px; letter-spacing: 0.5px; }
</style>
</head>
<body>
<main class="stationery">

  <section class="card card--front" aria-label="Business card front">
    <svg class="card__waves" viewBox="0 0 560 340" preserveAspectRatio="none" aria-hidden="true">
      <path d="M0 0 H190 C150 30 170 70 110 70 C50 70 40 95 0 100 Z" fill="var(--soft-grey)"/>
      <path d="M0 0 H170 C130 20 150 50 95 52 C40 54 30 75 0 80 Z" fill="var(--charcoal)"/>
      <path d="M560 250 C520 260 500 300 440 305 C390 310 370 330 360 340 H560 Z" fill="var(--mid-grey)"/>
      <path d="M560 270 C525 280 510 315 455 320 C420 323 400 335 395 340 H560 Z" fill="var(--charcoal)"/>
    </svg>
    <div class="brand">
      <span class="brand__dot"></span>
      <span class="brand__name">TOLVARIN</span>
    </div>
  </section>

  <section class="card card--back" aria-label="Business card back">
    <svg class="card__waves" viewBox="0 0 560 340" preserveAspectRatio="none" aria-hidden="true">
      <path d="M0 0 H70 C60 30 30 40 28 80 C26 110 10 120 0 125 Z" fill="var(--charcoal)"/>
      <path d="M0 210 C30 240 20 300 60 340 H0 Z" fill="var(--charcoal)"/>
      <path d="M560 200 C540 240 510 250 470 255 C420 262 400 310 380 340 H560 Z" fill="var(--soft-grey)"/>
      <path d="M560 225 C540 262 515 272 480 276 C440 282 420 320 405 340 H560 Z" fill="var(--charcoal)"/>
    </svg>
    <div class="brand">
      <span class="brand__dot"></span>
      <span class="brand__name">TOLVARIN</span>
    </div>
    <div class="contact">
      <p class="contact__name">Company Name</p>
      <p class="contact__role">Principal</p>
      <p class="contact__post">B Bus. Mktg, Grad Dip Digital Mktg, CPM</p>
      <p class="contact__line">mobile: 04XX-XXX-XXX</p>
      <p class="contact__line">email: info@tolvarin.com.au</p>
      <p class="contact__web">www.tolvarin.com.au</p>
    </div>
  </section>

</main>
</body>
</html>
```